New Wine Label - Classy, Simple, Modern

We are a small boutique winery who have been making and selling wine for 21 years. We are called "Calloway Ridge Winery" and Calloway is the Greek God of wine. We have a classic label at the moment that we would like to modernise.

We are looking to update our labels while keeping some of the original elements.
From existing label to definitely keep:
1. Logo (Colour can be darkened to a very dark purple - almost black)
2. Legal requirements - Front Label: 750ml, variety, year, "Canberra District" Back Label: Produce of Australia, number of standard drinks, alc/vol, additives, internet address, bar code plus new requirement to warn pregnant women alcohol can harm their babies.
From existing label open to change:
3. What would be nice - Separate front and back labels. Focus on logo on front label (Possibly printed in a raised gloss/embossed), Modern Font,
4. What can we lose? Happy to lose the words about us.
5.Font - Modern, Colour - white background, Shape Rectangular Front approximately height 11cm width 9cm & Back height 9cm width 7cm.

Prototype label can be for a
Front:
2022 Cabernet Sauvignon, Canberra District, 750ml, Estate Grown and Made
Back
13.6%ALC/VOL, APPROX 8.0 STANDARD DRINKS, PRESERVATIVE (220) ADDED, PRODUCE OF AUSTRALIA, Bar Code, Pregnant women warning, www.calloway-ridge.com.au

if you want to use some words to describe the wine that's fine - you can make some up or use existing words from our website www.calloway-ridge.com.au

Files:
1 - Photo of existing front label
2 - Current printers spec sheet for front and back label
3 - Pregnancy warning graphic (specific details see link below - label type 1)
4 - Current Bar Code for Cabernet Sauvignon
Many file types of existing logo

Link to legal requirement for pregnant women warning - we need label type 1 -https://www.examplelabelrules.org/industry/labelling/Pages/pregnancy-warning-labels-downloadable-files.aspx

Target Market(s)
25 - 40 year olds, drink wine

Industry/Entity Type
Winery - Wine Production

```html
<!DOCTYPE html>
<html lang="en">
<head>
<meta charset="UTF-8">
<title>Calloway Ridge Winery – Cabernet Sauvignon 2022 Front Label</title>
<link rel="stylesheet" href="https://fonts.googleapis.com/css2?family=Josefin+Sans:wght@400;500;600&display=swap">
<style>
  :root {
    --page-bg: #ffffff;
    --label-bg: #fafafa;
    --label-edge: #e6e6e6;
    --ink: #0b0a16;
    --emblem-dark: #0d0b22;
    --gold: #b8995c;
    --band: #0a0a0a;
    --band-text: #ffffff;
  }

  * { margin: 0; padding: 0; box-sizing: border-box; }

  html, body {
    width: 1200px;
    height: 1200px;
    overflow: hidden;
    background: var(--page-bg);
  }

  .canvas {
    position: relative;
    width: 1200px;
    height: 1200px;
  }

  .front-label {
    position: absolute;
    left: 175px;
    top: 80px;
    width: 850px;
    height: 1040px;
    background: var(--label-bg);
    border: 1px solid var(--label-edge);
    font-family: "Josefin Sans", sans-serif;
    color: var(--ink);
    text-align: center;
  }

  .label-texture {
    position: absolute;
    inset: 0 0 90px 0;
    background: radial-gradient(circle at 50% 45%, #ffffff 0%, #f6f6f6 100%);
  }

  .line {
    position: absolute;
    left: 0;
    width: 100%;
    line-height: 1;
    white-space: nowrap;
  }

  .region {
    top: 60px;
    font-size: 37px;
    font-weight: 500;
    letter-spacing: 0.14em;
  }

  .emblem {
    position: absolute;
    left: 249px;
    top: 138px;
    width: 352px;
    height: 352px;
  }

  .winery-name {
    top: 528px;
    font-size: 88px;
    font-weight: 500;
    letter-spacing: 0.16em;
    padding-left: 0.16em;
  }

  .winery-name-sub {
    top: 632px;
    font-size: 60px;
    font-weight: 500;
    letter-spacing: 0.14em;
    padding-left: 0.14em;
  }

  .variety {
    top: 756px;
    font-size: 32px;
    font-weight: 400;
    letter-spacing: 0.14em;
    color: var(--gold);
  }

  .estate {
    top: 818px;
    font-size: 27px;
    font-weight: 600;
    letter-spacing: 0.16em;
  }

  .vintage {
    top: 872px;
    font-size: 38px;
    font-weight: 500;
    letter-spacing: 0.14em;
    color: var(--gold);
  }

  .volume-band {
    position: absolute;
    left: 0;
    bottom: 0;
    width: 100%;
    height: 90px;
    background: var(--band);
    border-top: 4px solid var(--gold);
    border-bottom: 3px solid var(--gold);
    display: flex;
    align-items: center;
    justify-content: center;
  }

  .volume {
    color: var(--band-text);
    font-size: 42px;
    font-weight: 500;
    letter-spacing: 0.14em;
    padding-top: 6px;
  }
</style>
</head>
<body>
  <main class="canvas">
    <section class="front-label" aria-label="Front wine label">
      <div class="label-texture" role="img" aria-label="Fine white fingerprint-line texture across the label"></div>

      <p class="line region">CANBERRA DISTRICT</p>

      <svg class="emblem" viewBox="0 0 352 352" role="img" aria-label="Winery emblem">
        <circle cx="176" cy="176" r="176" fill="var(--emblem-dark)"/>
      </svg>

      <h1 class="line winery-name">CALLOWAY</h1>
      <p class="line winery-name-sub">RIDGE WINERY</p>

      <p class="line variety">CABERNET SAUVIGNON</p>
      <p class="line estate">ESTATE GROWN &amp; MADE</p>
      <p class="line vintage">2022</p>

      <div class="volume-band">
        <span class="volume">750 ML</span>
      </div>
    </section>
  </main>
</body>
</html>
```